creation of a business card design for a company specializing in the creation...

I would like to create a design for a professional business card on a black background and with the company's colors (I am attaching some files: including the logo in horizontal and centered format, I am also attaching a recent project design a T-shirt, this is the one I chose to give you an idea of my preferences.

we are in the process of developing a new website design, it is still in the development phase but it can be viewed at the following address: www.vantrelmo.be to give you other ideas about the company
you will see for yourself the subject of my main activity: company specializing in the construction of stairs

I would like a business card that stands out from the rest with a unique design

here is the informations
Name: Lucien Barthel
Function: Manager
Address: Rue Moulinet du Parc 42
7180 La Louvière
telephone: +32 468 219 804
email: info@rx7p.be
website: rx7p. be
social networks: Facebook, YouTube, TikTok, Instagram

Target Market(s)

customer who wants to have a beautiful staircase built

Industry/Entity Type

contruction d'escalier

Contact Information for Business Card

Adresse. Numero de telephone, site web, le texte : "Createur d'escalier", logo recto-verso, icone des reseaux sociaux

Requirements
Must have
• the mention: Stair creator
Nice to have
• an illustration of a designer staircase
Should not have
• do not distort the logo

```html
<!DOCTYPE html>
<html lang="en">
<head>
<meta charset="utf-8">
<title>RX7P business card – front and back</title>
<link href="https://fonts.googleapis.com/css2?family=Open+Sans:wght@400;700&display=swap" rel="stylesheet">
<style>
  :root {
    --page-bg: #e9e9ea;
    --card-black: #0b0b0c;
    --card-black-soft: #1c1c1e;
    --band-light: #8fb6cf;
    --band-mid: #5f8fac;
    --band-dark: #2c5a72;
    --stair-light: #a9c7dc;
    --stair-mid: #7fa6c0;
    --ink-white: #ffffff;
    --badge-blue: #4a7892;
  }
  * { box-sizing: border-box; margin: 0; padding: 0; }
  html, body {
    width: 1200px; height: 780px; overflow: hidden;
    background: var(--page-bg);
    font-family: "Open Sans", Arial, sans-serif;
  }
  .sheet {
    position: relative; width: 1200px; height: 780px;
    display: flex; align-items: center; justify-content: center; gap: 40px;
  }
  .card {
    position: relative; width: 540px; height: 350px;
    border-radius: 6px; overflow: hidden;
    background: linear-gradient(135deg, var(--card-black-soft) 0%, var(--card-black) 55%, #000 100%);
    box-shadow: 0 14px 30px rgba(0,0,0,.25);
  }

  /* brand lockup: invented name beside one plain circle, tagline below */
  .lockup { position: absolute; display: flex; flex-direction: column; align-items: center; }
  .brand {
    display: flex; align-items: center;
    color: var(--ink-white); font-weight: 700; letter-spacing: 2px;
  }
  .brand__circle { border-radius: 50%; background: var(--badge-blue); flex: none; }
  .tagline {
    color: var(--ink-white); font-weight: 700; text-transform: uppercase;
    letter-spacing: 1.5px; white-space: nowrap;
  }

  .card--front .lockup { left: 250px; top: 22px; gap: 8px; }
  .card--front .brand { gap: 14px; font-size: 32px; }
  .card--front .brand__circle { width: 70px; height: 70px; }
  .card--front .tagline { font-size: 12px; }

  .card--back .lockup { left: 50%; top: 50%; transform: translate(-50%, -50%); gap: 16px; }
  .card--back .brand { gap: 22px; font-size: 56px; }
  .card--back .brand__circle { width: 124px; height: 124px; }
  .card--back .tagline { font-size: 18px; }

  /* front: information band */
  .info-band {
    position: absolute; left: 0; right: 0; top: 146px; height: 112px;
    background: linear-gradient(90deg, var(--band-light) 0%, var(--band-mid) 55%, var(--band-dark) 100%);
  }
  .person { position: absolute; left: 22px; top: 10px; color: var(--ink-white); }
  .person__name { font-size: 25px; font-weight: 700; line-height: 1.2; white-space: nowrap; }
  .person__role { font-size: 16px; font-weight: 400; text-align: right; margin-top: 2px; }

  .stair-graphic {
    position: absolute; left: 246px; top: 12px; width: 66px; height: 88px;
    background: linear-gradient(160deg, var(--stair-light) 0%, var(--stair-mid) 100%);
    border-radius: 2px;
  }

  .contact-list {
    position: absolute; right: 20px; top: 24px; list-style: none;
    color: var(--ink-white); font-size: 16px; line-height: 25px;
  }
  .contact-list li { display: flex; align-items: center; gap: 8px; white-space: nowrap; }
  .contact-list svg { width: 14px; height: 14px; flex: none; }

  .address {
    position: absolute; left: 22px; top: 280px;
    color: var(--ink-white); font-size: 16px; line-height: 24px; white-space: nowrap;
  }
</style>
</head>
<body>
<main class="sheet">

  <section class="card card--front" aria-label="Business card front">
    <div class="lockup">
      <div class="brand">
        <span class="brand__circle"></span>
        <span class="brand__name">RX7P</span>
      </div>
      <p class="tagline">Créateur d'escalier</p>
    </div>

    <div class="info-band">
      <div class="person">
        <p class="person__name">Lucien Barthel</p>
        <p class="person__role">Manager</p>
      </div>
      <div class="stair-graphic" role="img" aria-label="Staircase graphic"></div>
      <ul class="contact-list">
        <li>
          <svg viewBox="0 0 24 24" fill="#fff" aria-hidden="true"><path d="M6.6 10.8a15.1 15.1 0 0 0 6.6 6.6l2.2-2.2a1 1 0 0 1 1-.25 11.4 11.4 0 0 0 3.6.57 1 1 0 0 1 1 1V20a1 1 0 0 1-1 1A17 17 0 0 1 3 4a1 1 0 0 1 1-1h3.5a1 1 0 0 1 1 1c0 1.25.2 2.450.57 3.57a1 1 0 0 1-.25 1z"/></svg>
          +32 468 219 804
        </li>
        <li>
          <svg viewBox="0 0 24 24" fill="none" stroke="#fff" stroke-width="2" aria-hidden="true"><rect x="3" y="5" width="18" height="14" rx="1"/><path d="M3 6l9 7 9-7"/></svg>
          info@rx7p.be
        </li>
        <li>
          <svg viewBox="0 0 24 24" fill="none" stroke="#fff" stroke-width="2" aria-hidden="true"><circle cx="12" cy="12" r="9"/><path d="M3 12h18M12 3c3 3 3 15 0 18M12 3c-3 3-3 15 0 18"/></svg>
          www.rx7p.be
        </li>
      </ul>
    </div>

    <p class="address">Rue Moulinet du Parc 42 7180 La Louvière</p>
  </section>

  <section class="card card--back" aria-label="Business card back">
    <div class="lockup">
      <div class="brand">
        <span class="brand__circle"></span>
        <span class="brand__name">RX7P</span>
      </div>
      <p class="tagline">Créateur d'escalier</p>
    </div>
  </section>

</main>
</body>
</html>
```